Norrell Advisory WA Business Card

Create an interesting, eye catching and colourful two sided business card. We are a business consulting operation assisting SME's improve all areas of their business. We provide consulting services to assist SME's to create a culture of continuous improvement, making a positive difference in the business. Our tag line is Small changes, big rewards. We want to create a well recognised, innovative brand that can be continued throughout our website, social media and email correspondence.

Target Market(s)

Small to Medium Enterprise Business Owners

Industry/Entity Type

Business Consultant

Contact Information for Business Card

Name of Business: Norrell Advisory - Steady Steps Lasting Results
Derek Holloway Ph 0407385510 Megan Holloway Ph 0407913847
Email norrelladvisorywa@mailbox-example.com
Web address TBA
FaceBook page TBA

BACKSIDE OF CARD

Providing assistance with:

• Organisation & Efficiency
• Revenue generation & Marketing
• Financial Management
• Production quality & delivery
• Systems & Process documentation
• Exit Strategy

Font styles to use
Other font styles liked:
• Calibri

Colors

Designer to choose colors to be used in the design.

Requirements
Must have
• Calibri font

```html
<!DOCTYPE html>
<html lang="en">
<head>
<meta charset="utf-8">
<title>Norrell Advisory WA – Business Card</title>
<link rel="stylesheet" href="https://fonts.googleapis.com/css2?family=Open+Sans:wght@400;600;700&family=Carlito:wght@400;700&display=swap">
<style>
  :root {
    --page: #e6e6e6;
    --card-white: #ffffff;
    --card-dark: #2e2e2e;
    --ink: #2f2f2f;
    --ink-soft: #4d4d4d;
    --ink-muted: #5c5c5c;
    --rule: #9a9a9a;
    --blue: #1b7dc2;
    --blue-bright: #1f8ad3;
    --green: #8cc63f;
    --yellow: #fbb32c;
    --red: #ee4534;
    --light-text: #f0f0f0;
  }
  * { box-sizing: border-box; margin: 0; padding: 0; }
  html, body { width: 1125px; height: 1200px; overflow: hidden; }
  body {
    background: var(--page);
    font-family: "Open Sans", "Carlito", sans-serif;
    position: relative;
  }
  .card {
    position: absolute;
    left: 157px;
    width: 825px;
    height: 472px;
    box-shadow: 0 2px 4px rgba(0,0,0,0.25);
    overflow: hidden;
  }
  .card--front { top: 106px; background: var(--card-white); }
  .card--back { top: 639px; background: var(--card-dark); }

  /* Front: brand block */
  .brand__mark {
    position: absolute;
    left: 607px;
    top: 80px;
    width: 62px;
    height: 62px;
    background: var(--blue);
  }
  .brand {
    position: absolute;
    right: 38px;
    top: 186px;
    display: flex;
    flex-direction: column;
    align-items: flex-end;
  }
  .brand__name {
    font-weight: 700;
    font-size: 30px;
    line-height: 1;
    color: var(--ink);
    letter-spacing: 0.2px;
  }
  .brand__tagline {
    font-weight: 400;
    font-size: 15.5px;
    line-height: 1.2;
    letter-spacing: 1.6px;
    color: var(--ink-muted);
    margin-top: 8px;
  }

  /* Front: people */
  .people {
    position: absolute;
    left: 41px;
    top: 299px;
    display: flex;
    gap: 34px;
  }
  .person__name {
    font-weight: 600;
    font-size: 27px;
    line-height: 1.1;
    color: var(--blue);
  }
  .person__phone {
    font-weight: 700;
    font-size: 17px;
    line-height: 1.2;
    color: var(--ink-soft);
    margin-top: 2px;
    padding-left: 2px;
  }
  .divider {
    position: absolute;
    left: 41px;
    top: 366px;
    width: 720px;
    height: 1px;
    background: var(--rule);
  }

  /* Front: contact rows */
  .contacts {
    position: absolute;
    left: 39px;
    top: 378px;
    font-size: 17px;
    color: var(--ink-muted);
  }
  .contact-row {
    display: flex;
    align-items: center;
    gap: 10px;
    height: 25px;
  }
  .contact-row svg { flex: none; }
  .contact-row .social { margin-left: 10px; }
  .social-square {
    width: 15px; height: 15px;
    background: var(--blue);
    flex: none;
  }

  /* Front: colour stripes */
  .stripes {
    position: absolute;
    left: 0; right: 0; bottom: 0;
    height: 9px;
    display: flex;
    gap: 3px;
  }
  .stripes span { flex: 1; }
  .stripe--green { background: linear-gradient(90deg, #7cbf3a, #a5cf4a); }
  .stripe--yellow { background: linear-gradient(90deg, #f7a02a, #f9d43c); }
  .stripe--blue { background: linear-gradient(90deg, #1a75b8, #4ba7dc); }
  .stripe--red { background: var(--red); }

  /* Back */
  .back-brand {
    position: absolute;
    left: 112px;
    top: 196px;
    width: 230px;
    text-align: center;
    font-weight: 700;
    font-size: 30px;
    line-height: 1.15;
    color: var(--light-text);
  }
  .services {
    position: absolute;
    left: 360px;
    top: 138px;
  }
  .services__title {
    font-weight: 700;
    font-size: 25px;
    color: var(--blue-bright);
    margin-bottom: 4px;
  }
  .services__list {
    list-style: none;
    font-family: "Carlito", "Open Sans", sans-serif;
    font-size: 19.5px;
    color: var(--light-text);
  }
  .services__list li {
    display: flex;
    align-items: center;
    height: 26px;
  }
  .services__list li::before {
    content: "";
    width: 7px; height: 7px;
    border-radius: 50%;
    background: var(--blue-bright);
    margin: 0 8px 0 2px;
    flex: none;
  }
</style>
</head>
<body>
  <section class="card card--front" aria-label="Business card front">
    <div class="brand__mark"></div>
    <div class="brand">
      <div class="brand__name">NORRELL ADVISORY</div>
      <div class="brand__tagline">STEADY STEPS LASTING RESULTS</div>
    </div>

    <div class="people">
      <div class="person">
        <div class="person__name">Derek Holloway</div>
        <div class="person__phone">0407385510</div>
      </div>
      <div class="person">
        <div class="person__name">Megan Holloway</div>
        <div class="person__phone">0407913847</div>
      </div>
    </div>

    <div class="divider"></div>

    <div class="contacts">
      <div class="contact-row">
        <svg width="16" height="12" viewBox="0 0 16 12" aria-hidden="true">
          <rect x="0.5" y="0.5" width="15" height="11" fill="none" stroke="#1b7dc2"/>
          <path d="M0.5 0.5 L8 7 L15.5 0.5" fill="none" stroke="#1b7dc2"/>
        </svg>
        <span>norrelladvisorywa@mailbox-example.com</span>
      </div>
      <div class="contact-row">
        <svg width="17" height="17" viewBox="0 0 17 17" aria-hidden="true">
          <circle cx="8.5" cy="8.5" r="8" fill="#1b7dc2"/>
          <path d="M4 5 Q7 4 8 7 Q6 9 7 12 M10 3 Q12 6 14 7 M11 11 Q13 10 14 12" fill="none" stroke="#fff" stroke-width="1.3"/>
        </svg>
        <span>www.norrelladvisorywa.example</span>
        <span class="social-square social"></span>
        <span>norrelladvisorywa</span>
      </div>
    </div>

    <div class="stripes">
      <span class="stripe--green"></span>
      <span class="stripe--yellow"></span>
      <span class="stripe--blue"></span>
      <span class="stripe--red"></span>
    </div>
  </section>

  <section class="card card--back" aria-label="Business card back">
    <div class="back-brand">NORRELL<br>ADVISORY</div>
    <div class="services">
      <h2 class="services__title">Providing assistance with</h2>
      <ul class="services__list">
        <li>Organisation &amp; Efficiency</li>
        <li>Revenue generation &amp; Marketing</li>
        <li>Financial Management</li>
        <li>Production quality &amp; delivery</li>
        <li>Systems &amp; Process documentation</li>
        <li>Exit Strategy</li>
      </ul>
    </div>
  </section>
</body>
</html>
```